Design my dad a new business card because his current one sucks!

I need a business card designed for my fathers home maintenance business. His customers are individuals (single moms, old people etc.) as well as the occasional business. As such it needs to be accessible to both target audiences.

The front of the card should be dark grey on yellow with the logo and contain the following information:
- Darren Holtwick
- 0488 274 915
- info@brightoakhomecare.com.au
- 0488 274 915

- ABN: 71 284 630 912
- 'Fully Insured'

The reverse should be yellow on dark grey and will have the web address:
- brightoakhomecare.com.au

And a few key services he offers:
GENERAL REPAIRS
PAINTING/TILING/
PAVING &CONCRETING
PRESSURE WASHING
ON-SITE WELDING
DECKING ADDITIONS & REPAIRS
FENCING
FULL BOND CLEANING

This will be first time the logo has been printed so you will need to come up with the best CMYK approximation of the RGB colours to make sure it is a close as possible.

```html
<!DOCTYPE html>
<html lang="en">
<head>
<meta charset="utf-8">
<title>Bright Oak Home Care – Business Cards</title>
<link rel="stylesheet" href="https://fonts.googleapis.com/css2?family=Source+Sans+3:wght@400;600;700&display=swap">
<style>
  :root {
    --page-bg: #8e8e8e;
    --charcoal: #3d3d3f;
    --charcoal-deep: #333335;
    --frame-grey: #4a4a4c;
    --yellow: #f7d200;
    --yellow-warm: #f4a900;
    --yellow-bright: #f6e800;
    --yellow-stripe: #efdc00;
    --text-dark: #2e2e30;
  }
  * { box-sizing: border-box; margin: 0; padding: 0; }
  html, body {
    width: 1200px; height: 1096px; overflow: hidden;
    background: var(--page-bg);
    font-family: "Source Sans 3", "Myriad Pro", Arial, sans-serif;
  }
  .canvas {
    position: relative; width: 1200px; height: 1096px;
    display: flex; flex-direction: column; align-items: center; justify-content: center; gap: 30px;
  }
  .card {
    position: relative; width: 820px; height: 502px; overflow: hidden;
    box-shadow: 0 6px 18px rgba(0,0,0,.25);
  }
  .panel { position: relative; width: 100%; height: 100%; overflow: hidden; }

  /* Front: dark grey on yellow */
  .card--front { background: var(--frame-grey); padding: 24px; }
  .card--front .panel {
    background: linear-gradient(135deg, var(--yellow) 0%, var(--yellow) 45%, var(--yellow-warm) 100%);
  }
  .watermark-light {
    position: absolute; left: 40px; top: 150px;
    font-size: 150px; font-weight: 700; line-height: 1; letter-spacing: -4px;
    color: rgba(255,255,255,.14); white-space: nowrap;
  }
  .holder-name {
    position: absolute; left: 36px; top: 22px;
    color: var(--text-dark); font-size: 36px; font-weight: 400; letter-spacing: .5px;
  }
  .brand {
    position: absolute; left: 36px; top: 110px;
    display: flex; align-items: center; gap: 12px;
    color: var(--text-dark); font-size: 38px; font-weight: 700; letter-spacing: -.5px;
  }
  .brand .mark { width: 34px; height: 34px; border-radius: 50%; background: var(--text-dark); }
  .contact {
    position: absolute; right: 36px; bottom: 26px;
    text-align right; text-align: right; color: var(--text-dark);
    font-size: 22px; line-height: 1.3; letter-spacing: .4px; font-style: normal;
  }

  /* Reverse: yellow on dark grey */
  .card--reverse {
    padding: 30px;
    background: repeating-linear-gradient(45deg, var(--yellow-bright) 0 4px, var(--yellow-stripe) 4px 8px);
  }
  .card--reverse .panel { background: var(--charcoal); }
  .services {
    position: absolute; top: 30px; list-style: none;
    color: var(--yellow); font-size: 18px; font-weight: 400;
    letter-spacing: 1.4px; line-height: 1.3; text-transform: uppercase;
  }
  .services--left { left: 36px; }
  .services--right { right: 36px; text-align: right; }
  .web-bar {
    position: absolute; left: 0; top: 200px; width: 440px; height: 48px;
    background: var(--charcoal-deep);
    color: var(--yellow); font-size: 22px; letter-spacing: .6px;
    display: flex; align-items: center; padding-left: 36px;
  }
  .watermark-dark {
    position: absolute; left: 36px; top: 290px;
    font-size: 130px; font-weight: 700; line-height: 1; letter-spacing: -4px;
    color: var(--charcoal-deep); white-space: nowrap;
  }
</style>
</head>
<body>
<main class="canvas">

  <section class="card card--front" aria-label="Card front">
    <div class="panel">
      <div class="watermark-light" aria-hidden="true">Bright Oak</div>
      <h1 class="holder-name">Darren Holtwick</h1>
      <div class="brand"><span class="mark" aria-hidden="true"></span>Bright Oak Home Care</div>
      <address class="contact">
        <div>0488 274 915</div>
        <div>info@brightoakhomecare.com.au</div>
        <div>0488 274 915</div>
        <div>ABN: 71 284 630 912</div>
        <div>“Fully Insured”</div>
      </address>
    </div>
  </section>

  <section class="card card--reverse" aria-label="Card reverse">
    <div class="panel">
      <div class="watermark-dark" aria-hidden="true">Bright Oak</div>
      <ul class="services services--left">
        <li>General Repairs</li>
        <li>Painting/Tiling/</li>
        <li>Paving &amp;Concreting</li>
        <li>Pressure Washing</li>
      </ul>
      <ul class="services services--right">
        <li>On-Site Welding</li>
        <li>Decking Additions &amp; Repairs</li>
        <li>Fencing</li>
        <li>Full Bond Cleaning</li>
      </ul>
      <div class="web-bar">brightoakhomecare.com.au</div>
    </div>
  </section>

</main>
</body>
</html>
```